Dental specialist needs a sharp looking letterhead

I am looking for a letterhead to be used to send letters and communication between myself (a dental specialist) and other dentists.
My office is a state of the art dental specialty office.
I need to letterhead to also state:
Bertram L. Oswick DDS
2748 Tollard Avenue, Suite K
West Tollard, NY 14391
(716)392-5061
fax: (716)392-5087
oswickroot.com (**this email address may change)

i included my logo designs.
thank you

Target Market(s)

dentists

Industry/Entity Type

Communication

Requirements
Must have
• the included logo, whether the vertical or horizontal versions

```html
<!DOCTYPE html>
<html lang="en">
<head>
<meta charset="utf-8">
<title>Keystone Endodontics P.C. — Letterhead</title>
<link href="https://fonts.googleapis.com/css2?family=Roboto+Slab:wght@400;700&display=swap" rel="stylesheet">
<style>
  :root {
    --ink: #2b2b2b;
    --black: #0b0b0b;
    --blue: #3f9fdb;
    --green: #8bc53f;
    --paper: #ffffff;
    --rule: #555555;
  }
  html, body { margin: 0; padding: 0; overflow: hidden; background: var(--paper); }
  .sheet {
    position: relative;
    width: 931px; height: 1200px;
    background: var(--paper);
    overflow: hidden;
    font-family: "Roboto Slab", Georgia, serif;
    color: var(--ink);
  }
  .brand {
    position: absolute; left: 28px; top: 30px;
    display: flex; flex-direction: column; align-items: center; gap: 12px;
    width: 130px;
  }
  .brand-dot { width: 70px; height: 70px; border-radius: 50%; background: var(--blue); }
  .brand-name {
    font-weight: 700; font-size: 15px; line-height: 1.2;
    color: var(--black); text-align: center;
  }
  .contact {
    position: absolute; left: 660px; top: 45px;
    border-left: 1px solid var(--rule);
    padding-left: 12px; height: 96px;
  }
  .contact-name { font-size: 21px; line-height: 1; margin: 2px 0 10px; font-weight: 400; }
  .contact-line { display: flex; align-items: center; gap: 5px; font-size: 15.5px; line-height: 21px; }
  .contact-line svg { width: 13px; height: 13px; flex: none; }
  .footer-rule {
    position: absolute; left: 0; right: 0; top: 1106px; height: 5px;
    background: var(--blue);
  }
  .footer-band {
    position: absolute; left: 0; right: 0; top: 1117px; bottom: 0;
    background: var(--green);
  }
  .address {
    position: absolute; right: 35px; top: 1132px;
    color: var(--paper); text-align: right; font-size: 18.5px; line-height: 23px;
  }
  .address-line { display: flex; align-items: center; justify-content: flex-end; gap: 8px; }
  .address-line svg { width: 13px; height: 17px; }
</style>
</head>
<body>
<div class="sheet">
  <div class="brand">
    <div class="brand-dot"></div>
    <div class="brand-name">Keystone Endodontics P.C.</div>
  </div>

  <div class="contact">
    <p class="contact-name">Bertram L. Oswick, DDS</p>
    <div class="contact-line">
      <svg viewBox="0 0 16 16" aria-hidden="true"><circle cx="8" cy="8" r="7" fill="none" stroke="var(--blue)" stroke-width="1.5"/><path d="M6 4c-1 1-1 4 1 6s4 2 5 1l-1.5-1.5-1 .7C8 9.5 7 8.5 6.5 7.3l.7-1L6 4z" fill="var(--blue)"/></svg>
      <span>716-392-5061</span>
    </div>
    <div class="contact-line">
      <svg viewBox="0 0 16 16" aria-hidden="true"><rect x="4" y="2" width="8" height="5" fill="var(--green)"/><rect x="1" y="6" width="14" height="6" rx="1.5" fill="var(--green)"/><rect x="3" y="12" width="3" height="2" fill="var(--green)"/><rect x="10" y="12" width="3" height="2" fill="var(--green)"/></svg>
      <span>716-392-5087</span>
    </div>
    <div class="contact-line">
      <svg viewBox="0 0 16 16" aria-hidden="true"><rect x="1" y="3.5" width="14" height="9" fill="var(--blue)"/><path d="M1 3.5l7 5 7-5" fill="none" stroke="#fff" stroke-width="1.2"/></svg>
      <span>office@oswickroot.com</span>
    </div>
  </div>

  <div class="footer-rule"></div>
  <div class="footer-band"></div>

  <div class="address">
    <div class="address-line">
      <svg viewBox="0 0 12 16" aria-hidden="true"><path d="M6 0C2.7 0 0 2.6 0 5.8 0 10 6 16 6 16s6-6 6-10.2C12 2.6 9.3 0 6 0zm0 8.2A2.3 2.3 0 1 1 6 3.6a2.3 2.3 0 0 1 0 4.6z" fill="#fff"/></svg>
      <span>2748 Tollard Avenue, Suite K</span>
    </div>
    <div>West Tollard, NY 14391</div>
  </div>
</div>
</body>
</html>
```